Harvest Gateway Fellowship Ministries needs a fresh new web design

We are an up and coming multicultural church that aims to bring people into a life changing encounter with God. We need a fresh and inviting website in order to increase our internet presence and make us easier to connect with.
Here are some of the basic requirements for the site:
• Clearly displayed address, service times, and contact info
• A staff profile page
• An area for a calendar with upcoming events and their details
• Social media buttons
• Group pages for the different ministries (youth, children’s church, men, etc…)
• An area for donations and eCommerce
• A resources page for assorted media (podcasts, sermons, videos, etc.…)
• An area for prayer requests.

```html
<!DOCTYPE html>
<html lang="en">
<head>
<meta charset="utf-8">
<title>News and Events – Harvest Gateway Fellowship Ministries</title>
<link href="https://fonts.googleapis.com/css2?family=Lato:wght@300;400;700&display=swap" rel="stylesheet">
<style>
:root{
  --blue:#1e1291;
  --blue-top:#1c1590;
  --gold:#e6c214;
  --gold-text:#dcb300;
  --page:#f1f0ee;
  --ink:#555;
  --ink-dark:#333;
  --body:#777;
  --rule:#d9cfae;
  --icon:#9a9a9a;
  --footer-text:#c9c6f2;
}
*{box-sizing:border-box;margin:0;padding:0}
html,body{width:956px;height:1200px;overflow:hidden}
body{font-family:'Lato',sans-serif;background:var(--page);position:relative;color:var(--body)}
.abs{position:absolute}
a{text-decoration:none;color:inherit}

.topbar{left:0;top:0;width:956px;height:32px;background:var(--blue-top);color:#fff}
.topbar .motto{left:80px;top:9px;font-size:11.5px}
.topbar .sched-label{left:586px;top:9px;font-size:11.5px}
.topbar .sched-div{left:734px;top:6px;width:1px;height:20px;background:#fff}
.topbar .sched{left:743px;top:4px;font-size:9.5px;line-height:11px}

.header{left:0;top:32px;width:956px;height:92px;background:#fff}
.brand{left:80px;top:14px;width:194px;height:57px;display:flex;align-items:center;gap:7px}
.brand .dot{width:34px;height:34px;border-radius:50%;background:var(--gold);flex:none}
.brand .name{color:var(--blue);font-weight:700;font-size:13px;line-height:15px}
.hinfo{text-align:right;font-size:11px;line-height:12px;color:var(--ink)}
.hinfo h4{font-size:13px;font-weight:700;color:var(--ink);margin-bottom:3px}
.hinfo a{color:var(--gold-text);font-size:9.5px}
.hdiv{top:22px;width:1px;height:52px;background:#ccc}
.social{width:21px;height:21px;border-radius:50%;background:var(--icon)}

.nav{left:0;top:124px;width:956px;height:32px;background:var(--gold);border-top:2px solid #cfa90a}
.nav ul{list-style:none;display:flex;position:absolute;left:80px;top:0;height:30px;align-items:center}
.nav li{font-size:12px;color:#4a3e12;padding:0 11px;position:relative}
.nav li+li::before{content:"";position:absolute;left:0;top:1px;width:1px;height:13px;background:#c8a40b}

.banner{left:0;top:156px;width:956px;height:80px;background:linear-gradient(90deg,#2a1b08,#5a3c10 30%,#3a270a 60%,#24180a)}
.banner .crumb{left:80px;top:22px;font-size:10.5px;color:#ddd}
.banner .crumb b{color:#fff;font-weight:400}
.banner h1{left:80px;top:36px;font-size:20px;font-weight:700;color:#fff}

.sec-title{font-size:19px;font-weight:300;color:var(--gold-text);letter-spacing:.2px}
.sec-rule{height:1px;background:var(--rule)}
.month{font-size:15px;font-weight:700;color:#222}
.arrowbtn{width:13px;height:13px;background:#c9c9c9;border-radius:2px}

.photo{width:160px;height:99px;border-radius:3px;background:linear-gradient(135deg,#c9b8a6,#8c9fb7 50%,#9ec38a)}
.ntitle{font-size:14.5px;font-weight:700;color:var(--ink);line-height:16px}
.ntext{font-size:10.5px;line-height:16px;color:var(--body)}
.more{font-size:11px;color:var(--gold-text)}

.edate{font-size:24px;color:var(--gold-text);line-height:26px}
.edate b{font-weight:700}
.edate span{font-weight:300}
.etitle{font-size:15.5px;font-weight:700;color:var(--ink)}
.esep{height:1px;border-top:1px dashed #ddd}

.footer{left:0;top:958px;width:956px;height:242px;background:var(--blue);color:var(--footer-text)}
.footer h3{font-size:15px;font-weight:400;color:#fff;text-transform:uppercase;position:absolute;top:34px}
.ftext{font-size:10.5px;line-height:14.5px}
.flist{list-style:none;font-size:10.5px;line-height:19px}
.flist li::before{content:"• "}
.email-field{left:477px;top:81px;width:182px;height:27px;background:#fff;border-radius:3px;font-size:10.5px;color:#bbb;padding:8px 10px}
.subscribe{left:478px;top:116px;width:74px;height:27px;background:var(--gold);border-radius:3px;font-size:10.5px;color:#222;text-align:center;line-height:27px}
.fsocial{width:26px;height:26px;border-radius:50%;background:#a49fd3}
.frule{left:79px;top:181px;width:798px;height:1px;background:#3a2ea3}
.copy{left:0;top:195px;width:956px;text-align:center;font-size:9.5px;letter-spacing:.3px}
</style>
</head>
<body>

<div class="abs topbar">
  <div class="abs motto">A house of prayer for all nations, where the love, the presence and the power of God are real.</div>
  <div class="abs sched-label">SUNDAY SERVICE SCHEDULE</div>
  <div class="abs sched-div"></div>
  <div class="abs sched">09:00 A.M. | Sunday School<br>10:30 A.M. | Convergent Service</div>
</div>

<header class="abs header">
  <div class="abs brand">
    <span class="dot"></span>
    <span class="name">Harvest Gateway<br>Fellowship Ministries</span>
  </div>
  <div class="abs hinfo" style="right:500px;top:20px">
    <h4>Donate</h4>Lorem Ipsum is simply<br>dummy text of the printing<br><a href="#">Donate Now »</a>
  </div>
  <div class="abs hdiv" style="left:472px"></div>
  <div class="abs hinfo" style="right:276px;top:20px">
    <h4>Request Prayer</h4>Lorem Ipsum is simply dummy text<br>of the printing and typesetting industry.<br><a href="#">Request Now »</a>
  </div>
  <div class="abs hdiv" style="left:697px"></div>
  <div class="abs hinfo" style="right:134px;top:20px">
    <h4>Address</h4>Harvest Gateway<br>City, Location<br><a href="#">Contact »</a>
  </div>
  <div class="abs hdiv" style="left:838px"></div>
  <div class="abs social" style="left:855px;top:23px" role="img" aria-label="Social link"></div>
  <div class="abs social" style="left:855px;top:48px" role="img" aria-label="Social link"></div>
</header>

<nav class="abs nav">
  <ul>
    <li>Home</li><li>About</li><li>Staff Profile</li><li>News and Events</li><li>Worship &amp; Services</li><li>Groups</li><li>Shop</li><li>Resources</li><li>Contact</li>
  </ul>
</nav>

<div class="abs banner" role="img" aria-label="Warm golden wheat field backdrop">
  <div class="abs crumb">Home &gt; <b>News and Events</b></div>
  <h1 class="abs">News and Events</h1>
</div>

<!-- Latest news -->
<div class="abs sec-title" style="left:87px;top:279px">LATEST NEWS</div>
<div class="abs sec-rule" style="left:87px;top:305px;width:372px"></div>

<div class="abs photo" style="left:87px;top:330px" role="img" aria-label="Group of young people studying together"></div>
<div class="abs ntitle" style="left:262px;top:328px;width:200px">Lorem Ipsum is simply dummy text of the printing.</div>
<div class="abs ntext" style="left:262px;top:362px;width:195px">Lorem Ipsum is simply dummy text of the printing and typesetting industry. Lorem Ipsum has been the industry's..</div>
<div class="abs more" style="left:263px;top:418px">Read more.</div>

<div class="abs ntitle" style="left:87px;top:451px;width:360px">Lorem Ipsum is simply dummy text of the printing and typesetting industry.</div>
<div class="abs ntext" style="left:87px;top:485px;width:372px">Lorem Ipsum has been the industry's standard dummy text ever since the 1500s, when an unknown printer took a galley of type and scrambled it to make a type specimen book. It has survived not only five centuries..</div>
<div class="abs more" style="left:87px;top:541px">Read more.</div>

<div class="abs photo" style="left:87px;top:575px" role="img" aria-label="Group of young people studying together"></div>
<div class="abs ntitle" style="left:262px;top:573px;width:200px">Lorem Ipsum is simply dummy text of the printing.</div>
<div class="abs ntext" style="left:262px;top:608px;width:195px">Lorem Ipsum is simply dummy text of the printing and typesetting industry. Lorem Ipsum has been the industry's..</div>
<div class="abs more" style="left:263px;top:664px">Read more.</div>

<div class="abs ntitle" style="left:87px;top:696px;width:360px">Lorem Ipsum is simply dummy text of the printing and typesetting industry.</div>
<div class="abs ntext" style="left:87px;top:730px;width:372px">Lorem Ipsum has been the industry's standard dummy text ever since the 1500s, when an unknown printer took a galley of type and scrambled it to make a type specimen book. It has survived not only five centuries..</div>
<div class="abs more" style="left:87px;top:786px">Read more.</div>

<div class="abs ntitle" style="left:87px;top:811px;width:360px">Lorem Ipsum is simply dummy text of the printing and typesetting industry.</div>
<div class="abs ntext" style="left:87px;top:845px;width:372px">Lorem Ipsum has been the industry's standard dummy text ever since the 1500s, when an unknown printer took a galley of type and scrambled it to make a type specimen book. It has survived not only five centuries..</div>
<div class="abs more" style="left:87px;top:901px">Read more.</div>

<!-- Upcoming events -->
<div class="abs sec-title" style="left:497px;top:279px">UPCOMING EVENTS</div>
<div class="abs month" style="left:795px;top:282px">JULY</div>
<svg class="abs" style="left:839px;top:284px" width="30" height="14" viewBox="0 0 30 14" aria-hidden="true">
  <rect x="0" y="0" width="13" height="13" rx="2" fill="#c9c9c9"/><path d="M8 3.5 4.5 6.5 8 9.5" stroke="#fff" stroke-width="1.6" fill="none"/>
  <rect x="16" y="0" width="13" height="13" rx="2" fill="#c9c9c9"/><path d="M21 3.5 24.5 6.5 21 9.5" stroke="#fff" stroke-width="1.6" fill="none"/>
</svg>
<div class="abs sec-rule" style="left:497px;top:305px;width:372px"></div>

<div class="abs edate" style="left:498px;top:327px"><b>29</b> <span>JUL</span></div>
<div class="abs etitle" style="left:499px;top:353px">Vacation Bible School</div>
<div class="abs ntext" style="left:498px;top:373px;width:368px">Lorem Ipsum has been the industry's standard dummy text ever since the 1500s, when an unknown printer took a galley of type and scrambled it to make a type specimen book.</div>
<div class="abs more" style="left:499px;top:430px">View Details »</div>
<div class="abs esep" style="left:497px;top:457px;width:370px"></div>

<div class="abs edate" style="left:498px;top:470px"><b>20</b> <span>JUL</span></div>
<div class="abs etitle" style="left:499px;top:496px">Vacation Bible School</div>
<div class="abs ntext" style="left:498px;top:516px;width:368px">Lorem Ipsum has been the industry's standard dummy text ever since the 1500s, when an unknown printer took a galley of type and scrambled it to make a type specimen book.</div>
<div class="abs more" style="left:499px;top:573px">View Details »</div>
<div class="abs esep" style="left:497px;top:600px;width:250px"></div>

<div class="abs edate" style="left:498px;top:612px"><b>12</b> <span>JUL</span></div>
<div class="abs etitle" style="left:499px;top:638px">Vacation Bible School</div>
<div class="abs ntext" style="left:498px;top:658px;width:368px">Lorem Ipsum has been the industry's standard dummy text ever since the 1500s, when an unknown printer took a galley of type and scrambled it to make a type specimen book.</div>
<div class="abs more" style="left:499px;top:715px">View Details »</div>
<div class="abs esep" style="left:497px;top:742px;width:250px"></div>

<div class="abs edate" style="left:498px;top:755px"><b>07</b> <span>JUL</span></div>
<div class="abs etitle" style="left:499px;top:781px">Vacation Bible School</div>
<div class="abs ntext" style="left:498px;top:801px;width:368px">Lorem Ipsum has been the industry's standard dummy text ever since the 1500s, when an unknown printer took a galley of type and scrambled it to make a type specimen book.</div>
<div class="abs more" style="left:499px;top:858px">View Details »</div>

<footer class="abs footer">
  <h3 style="left:79px">Contact Us</h3>
  <div class="abs ftext" style="left:80px;top:62px">Harvest Gateway<br>Location, city<br>State Name, Country</div>
  <svg class="abs" style="left:80px;top:115px" width="12" height="12" viewBox="0 0 12 12" aria-hidden="true"><path d="M2.5 1 4.5 3.5 3.5 5c.8 1.6 1.9 2.7 3.5 3.5L8.5 7.5 11 9.5 10 11C5.5 11 1 6.5 1 2z" fill="#c9c6f2"/></svg>
  <div class="abs ftext" style="left:99px;top:114px;font-size:11px">+1 888-555-0142</div>
  <svg class="abs" style="left:80px;top:133px" width="13" height="10" viewBox="0 0 13 10" aria-hidden="true"><rect x=".5" y=".5" width="12" height="9" fill="#c9c6f2"/><path d="M.5.5 6.5 5.5 12.5.5" stroke="#1e1291" fill="none"/></svg>
  <div class="abs ftext" style="left:99px;top:130px;font-size:11px">hello@harvestgateway.example</div>

  <h3 style="left:255px">Communities We Serve</h3>
  <ul class="abs flist" style="left:257px;top:59px"><li>Lorem Ipsum</li><li>Dummy Links</li><li>More dummy</li><li>Sample Text</li><li>More samples</li></ul>
  <ul class="abs flist" style="left:344px;top:59px"><li>type text dummy</li><li>Lorem Ipsum</li></ul>

  <h3 style="left:477px">Newsletter</h3>
  <div class="abs ftext" style="left:477px;top:62px">Enter your email below to get notified</div>
  <div class="abs email-field">Your Email</div>
  <div class="abs subscribe">Subscribe</div>

  <h3 style="left:698px">Connect With Us</h3>
  <div class="abs ftext" style="left:698px;top:62px;width:185px">Stay connected for the latest updates at Harvest Gateway Fellowship</div>
  <div class="abs fsocial" style="left:699px;top:95px" role="img" aria-label="Social link"></div>
  <div class="abs fsocial" style="left:731px;top:95px" role="img" aria-label="Social link"></div>

  <div class="abs frule"></div>
  <div class="abs copy">Copyright © 2014. All rights reserved. Harvest Gateway Fellowship Ministries.</div>
</footer>

</body>
</html>
```